Maple Grove Youngsters Guild Business Card Project

We are a Minneapolis based discount club that caters to families with children. We need a business card that can be used to communicate our contact information to other businesses that may wish to offer discounts on our website.

Please use placeholders for contact information (i.e. John Doe, 123 Any Street, Any Town, etc.) and include spaces for the following: Full name, title, email, phone number, website, one line street address, city, state, and zip code.
Updates

Project Deadline Extended
Reason: I have extended the deadline because I had not intended the project to close so quickly.

Target Market(s)

Most of the time the business cards will be used in business to business situations. However, from time to time they may be distributed to our end customer, families with children.

Industry/Entity Type

Club

Font styles to use
Serif
Sans Serif
Other font styles liked:
• Open to suggestions

Requirements
Nice to have
• We might use the reverse side of the card as the design for our membership card.

```html
<!DOCTYPE html>
<html lang="en">
<head>
<meta charset="utf-8">
<title>Maple Grove Youngsters Guild — Business Card</title>
<link rel="stylesheet" href="https://fonts.googleapis.com/css2?family=Archivo+Black&family=Fira+Sans+Condensed:wght@300;400;600;800&display=swap">
<style>
  :root {
    --backdrop: #e9e6e2;
    --band-top: #5a5a5a;
    --band-bottom: #2b2b2b;
    --card-white: #ffffff;
    --ink: #3a3a3a;
    --ink-soft: #6b6b6b;
    --accent-green: #6cbf2e;
    --photo-light: #e6f0f8;
    --photo-mid: #a9c9e6;
    --photo-warm: #e9cfa8;
  }
  * { box-sizing: border-box; margin: 0; padding: 0; }
  html, body { width: 1200px; height: 840px; overflow: hidden; }
  body {
    background: var(--backdrop);
    font-family: "Fira Sans Condensed", sans-serif;
    color: var(--ink);
    position: relative;
  }
  .card {
    position: absolute;
    top: 266px;
    width: 540px;
    height: 309px;
    background: var(--card-white);
    overflow: hidden;
    box-shadow: 0 8px 24px rgba(0,0,0,0.18);
  }
  .card--front { left: 40px; }
  .card--back { left: 620px; }
  .card__band {
    position: absolute;
    left: 0; top: 0; right: 0;
    height: 94px;
    background: linear-gradient(180deg, var(--band-top), var(--band-bottom));
  }
  .club-name {
    font-weight: 800;
    color: var(--card-white);
    font-size: 15px;
    line-height: 1.1;
    display: flex;
    align-items: center;
    gap: 8px;
  }
  .club-name__dot {
    width: 14px; height: 14px;
    border-radius: 50%;
    background: var(--accent-green);
    flex: none;
  }
  .card--front .club-name {
    position: absolute;
    left: 22px; top: 30px;
    width: 170px;
  }
  .photo {
    position: absolute;
    right: 0; bottom: 0;
    width: 230px; height: 215px;
    background: radial-gradient(ellipse at 45% 35%, var(--photo-warm) 0%, var(--photo-mid) 45%, var(--photo-light) 100%);
  }
  .person {
    position: absolute;
    left: 30px; top: 124px;
    font-size: 16px;
    font-weight: 600;
    letter-spacing: 0.2px;
  }
  .person__title {
    font-weight: 300;
    font-size: 13px;
    color: var(--ink-soft);
    margin-left: 4px;
  }
  .contact {
    position: absolute;
    left: 22px; top: 206px;
    width: 280px;
    font-style: normal;
    font-size: 14px;
    line-height: 1.4;
    color: var(--ink);
  }
  .contact strong { font-weight: 600; }
  .card--back .club-name {
    position: absolute;
    left: 0; right: 0; top: 60px;
    justify-content: center;
    font-size: 18px;
  }
  .brand {
    position: absolute;
    left: 0; right: 0; top: 130px;
    text-align: center;
  }
  .brand__headline {
    font-family: "Archivo Black", sans-serif;
    font-size: 34px;
    color: var(--ink);
    line-height: 1;
  }
  .brand__headline span { color: var(--accent-green); }
  .brand__site {
    margin-top: 6px;
    font-size: 14px;
    font-weight: 800;
    color: var(--ink);
  }
</style>
</head>
<body>
  <section class="card card--front" aria-label="Business card front">
    <div class="card__band"></div>
    <div class="club-name"><span class="club-name__dot"></span>Maple Grove Youngsters Guild</div>
    <div class="photo" role="img" aria-label="Photo of a smiling family with three young children in light blue clothing"></div>
    <p class="person">JOHN DOE<span class="person__title">manager</span></p>
    <address class="contact">
      48 Birchwood Lane, Any Town MN 55311<br>
      <strong>tel:</strong> 555 0142 &nbsp;- &nbsp;<strong>fax:</strong> 555 0143<br>
      <strong>email:</strong> john@mailbox.test
    </address>
  </section>

  <section class="card card--back" aria-label="Business card back">
    <div class="card__band"></div>
    <div class="club-name"><span class="club-name__dot"></span>Maple Grove Youngsters Guild</div>
    <div class="brand">
      <p class="brand__headline">Your <span>Business</span></p>
      <p class="brand__site">www.yourclubsite.test</p>
    </div>
  </section>
</body>
</html>
```